IT company developing solutions for air cargo industry is looking for a new website

We are a professional IT company developing solutions for air cargo industry worldwide.

We are looking to update and completely redesign our current webpages: https://www.brisklane.cz/

What we like about our current pages are the animated graphics on the home page. These could stay, but not a must.

The design of the new pages should be very modern, clean, unique, creative, professional, and to make a statement. We are looking for animated graphics, cool and interesting interactions, cascading layers, etc.

Our company logo is yellow, gray and black. You don’t necessarily have to stick to this colour scheme, however the corporate colors should work well with the overal design of the web pages.
Dark mode pages are also an option.

The scope of the project would include creating a:

• Header
• Footer
• Landing page
• Navigation bar (8 tabs)
• Subpages (10)

In the first stage we are looking only for the header / footer / landing page with navigaton bar / Solutions page design.
As a second round, finalists might be asked to submit another section of the website to see their consistency in terms of the look and feel proposed for the Homepage and Solutions’ pages.
The winning designer will then complete the rest of the pages.

Attached you will find a brief for the first scope of the project. Please read the note section on slide nr. 3 carefully to understand, what we exactly are looking for to achieve.

Industry/Entity Type

Aviation

Number of Pages Required

1 page

Requirements
Must have
• See brief
Nice to have
• See brief
Should not have
• See brief

```html
<!DOCTYPE html>
<html lang="en">
<head>
<meta charset="utf-8">
<title>Brisk Lane – Air Cargo IT Solutions</title>
<link href="https://fonts.googleapis.com/css2?family=Fira+Sans+Condensed:wght@400;600;700&family=Lato:wght@400;700&display=swap" rel="stylesheet">
<style>
:root{
  --navy:#0f2231;
  --navy-deep:#0a1822;
  --yellow:#f8c512;
  --ink:#111111;
  --grey:#555555;
  --white:#ffffff;
  --footer:#15191c;
}
*{margin:0;padding:0;box-sizing:border-box}
html,body{width:1200px;height:2924px;overflow:hidden;background:var(--white)}
body{font-family:"Lato",sans-serif;color:var(--ink);position:relative}
.head{font-family:"Fira Sans Condensed",sans-serif}

.hero{position:absolute;left:0;top:0;width:1200px;height:1032px;
  background:linear-gradient(180deg,var(--navy-deep) 0%,var(--navy) 45%,#14283a 100%);
  border-top:3px solid var(--yellow)}
.hero-backdrop{position:absolute;left:0;top:300px;width:1200px;height:732px;
  background:linear-gradient(180deg,rgba(40,60,75,0) 0%,rgba(45,66,82,.45) 60%,rgba(30,48,62,.3) 100%)}
.nav{position:absolute;left:111px;top:38px;width:980px;height:50px;display:flex;align-items:center}
.brand{display:flex;align-items:center;gap:10px;color:var(--white);font-size:26px;font-weight:400}
.brand-mark{width:30px;height:30px;background:var(--yellow)}
.nav-links{display:flex;gap:29px;margin-left:auto;list-style:none;font-size:14.5px;color:var(--white)}
.hero-tagline{position:absolute;left:0;top:170px;width:1200px;text-align:center;color:var(--yellow);
  font-size:40px;font-weight:600;letter-spacing:1.5px;line-height:69px}
.hero-title{position:absolute;left:111px;top:366px;width:520px;color:var(--white);font-size:47px;font-weight:700;letter-spacing:1.5px;line-height:68px}
.hero-text{position:absolute;left:111px;top:651px;width:500px;color:var(--white);font-size:19px;line-height:45px}
.btn{position:absolute;display:flex;align-items:center;justify-content:center;background:var(--yellow);color:var(--ink);
  font-weight:700;font-size:16px;border-radius:24px}
.hero .btn{left:111px;top:905px;width:135px;height:45px}
.hero-visual{position:absolute;left:620px;top:400px;width:540px;height:530px;
  background:radial-gradient(ellipse at 50% 50%,rgba(38,140,170,.55) 0%,rgba(25,95,125,.35) 40%,rgba(15,34,49,0) 70%)}

.slogan{position:absolute;left:0;top:1032px;width:1200px;height:149px;background:var(--yellow);
  text-align:center;font-size:35px;font-weight:600;line-height:59px;padding-top:15px;letter-spacing:.5px}

.facts-title{position:absolute;left:0;top:1254px;width:1200px;text-align:center;font-size:46px;font-weight:700;letter-spacing:1px}
.card{position:absolute;width:307px;height:244px;border-radius:20px;text-align:center;padding-top:70px;
  box-shadow:0 4px 14px rgba(0,0,0,.05)}
.card.c1{background:linear-gradient(135deg,#fffdf5,#fdf0c3)}
.card.c2{background:linear-gradient(135deg,#fdf3cd,#fbe08a)}
.card.c3{background:linear-gradient(135deg,#fbe9a8,#fbe08a)}
.num{font-size:52px;font-weight:700;line-height:56px}
.num sup{font-size:26px;vertical-align:top;position:relative;top:-4px}
.label{font-size:21px;color:var(--grey);line-height:33px;margin-top:8px;padding:0 24px;letter-spacing:.5px}

.about-photo{position:absolute;left:0;top:1980px;width:620px;height:620px;
  background:radial-gradient(ellipse at 40% 50%,#dfe6ef 0%,#eef2f6 45%,#ffffff 75%)}
.about-title{position:absolute;left:632px;top:2016px;font-size:46px;font-weight:700;letter-spacing:1.5px}
.about-text{position:absolute;left:632px;top:2092px;width:460px;font-size:13.5px;color:var(--grey);line-height:27px}
.about-text p+p{margin-top:27px}
.about .btn{left:632px;top:2456px;width:135px;height:44px}

.footer{position:absolute;left:0;top:2627px;width:1200px;height:297px;background:var(--footer)}
.footer .brand{position:absolute;left:0;top:60px;width:1200px;justify-content:center;font-size:38px;gap:14px}
.footer .brand-mark{width:40px;height:40px}
.footer-links{position:absolute;left:0;top:155px;width:1200px;display:flex;justify-content:center;gap:29px;list-style:none;color:var(--white);font-size:14.5px}
.social{position:absolute;left:0;top:2834px;width:1200px;display:flex;justify-content:center;gap:10px}
.social span{width:28px;height:28px;background:var(--yellow);border-radius:4px}
.copy{position:absolute;left:0;top:2887px;width:1200px;text-align:center;color:var(--white);font-size:11px}
</style>
</head>
<body>
<header class="hero">
  <div class="hero-backdrop" role="img" aria-label="Faded city skyline behind the hero"></div>
  <nav class="nav">
    <div class="brand"><span>Brisk Lane</span><span class="brand-mark"></span></div>
    <ul class="nav-links">
      <li>Industries</li><li>Solutions ⌄</li><li>Operational Support</li><li>Case Studies</li><li>Testimonials</li><li>News</li><li>About ⌄</li>
    </ul>
  </nav>
  <h1 class="hero-tagline head">AFFORDABLE IT SOLUTIONS THAT REVOLUTIONIZE<br>TOMORROW'S AIR CARGO TODAY</h1>
  <h2 class="hero-title head">SEAMLESSLY<br>CONNECTING THE AIR<br>CARGO INDUSTRY FROM<br>MANILA TO TAHITI</h2>
  <p class="hero-text">Blending decades of air cargo knowledge with<br>end-to-end IT solutions. Whether you are an Airline,<br>GSA, GHA, Forwarder or E-commerce Operator, our<br>expertise can elevate your daily workflows, cutting down<br>on expenses, time, and errors.</p>
  <div class="btn">Learn More</div>
  <div class="hero-visual" role="img" aria-label="Glowing digital globe with air cargo route markers"></div>
</header>

<section class="slogan head">We are not IT tech experts attempting to do cargo! We are<br>cargo experts with programming skills!</section>

<section class="facts">
  <h2 class="facts-title head">FACTS</h2>
  <div class="card c1" style="left:113px;top:1355px"><div class="num">2014</div><div class="label head">Established</div></div>
  <div class="card c2" style="left:447px;top:1355px"><div class="num">22</div><div class="label head">Employees</div></div>
  <div class="card c3" style="left:780px;top:1355px"><div class="num">11,500,000<sup>+</sup></div><div class="label head">Nr. of Annual Electronic Exchanges</div></div>
  <div class="card c1" style="left:113px;top:1633px"><div class="num">18</div><div class="label head">Countries covered</div></div>
  <div class="card c2" style="left:447px;top:1633px"><div class="num">20<sup>+</sup></div><div class="label head">Connected Clients</div></div>
  <div class="card c3" style="left:780px;top:1633px"><div class="num">350,000<sup>+</sup></div><div class="label head">Nr. of Annual AWBs</div></div>
</section>

<section class="about">
  <div class="about-photo" role="img" aria-label="Passenger jet taking off over a misty cargo port"></div>
  <h2 class="about-title head">ABOUT US</h2>
  <div class="about-text">
    <p>On the other hand, we denounce with righteous indignation and dislike men who are so beguiled and demoralized by the charms of pleasure of the moment, so blinded by desire, that they cannot foresee the pain and trouble that are bound to ensue; and equal blame belongs to those who fail in their duty through weakness of will, which is the same as saying through shrinking from toil and pain. These cases are perfectly simple and easy to distinguish. In a free hour, when our power of choice is untrammelled and when nothing prevents our being able to do what</p>
    <p>But in certain circumstances and owing to the claims of duty or the obligations of business it will frequently occur that pleasures have to be repudiated and annoyances accepted.</p>
  </div>
  <div class="btn">Read More</div>
</section>

<footer class="footer">
  <div class="brand"><span>Brisk Lane</span><span class="brand-mark"></span></div>
  <ul class="footer-links">
    <li>Industries</li><li>Solutions</li><li>Operational Support</li><li>Case Studies</li><li>Testimonials</li><li>News</li><li>About Us</li>
  </ul>
</footer>
<div class="social"><span></span><span></span><span></span><span></span></div>
<div class="copy">(C) Copyright 2024 | All Rights Reserved</div>
</body>
</html>
```